KAJU Freightways #ALLKAJU Business Cards & Letterhead

I am looking to business cards designed for our organization. We are currently undergoing a small re-branding that is taking place. Our organization is called KAJU Freightways and we are headquartered in Phoenix, AZ. We primarily provide transportation and logistics services to the Marlow Parcel Bureau who is our largest customer. I would like to see a design that incorporates name, title, contact info, website, and address (this will be different depending on the employee). I would also like to see some color on the business card using our logo colors or a variation. I would like our logo on the back of the business card with the website displayed. The final design should communicate that we are a next generation transportation operate that focuses on being driver-first, customer-centric, innovative, and sustainable.We would also like our #ALLKAJU catch phrase incorporated as well.

Target Market(s)

Transportation & Logistics

Industry/Entity Type

Trucking Company

Contact Information for Business Card

-First and Last Name
-Position Title
-Contact Phone
-Contact Email
-Physical Address

Font styles to use
Serif

Colors

Designer to choose colors to be used in the design.

Requirements
Must have
• -KAJU logo prominently displayed
• -#ALLKAJU catch phrase used
• -Some amount of color, design gradient, etc.
• -Logo on the back with website listed (https://www.kajufreightco.example)

```html
<!DOCTYPE html>
<html lang="en">
<head>
<meta charset="utf-8">
<title>KAJU Freightways Business Card</title>
<link href="https://fonts.googleapis.com/css2?family=Lato:ital,wght@0,400;0,700;0,900;1,900&display=swap" rel="stylesheet">
<style>
  :root {
    --backdrop: #4d4d4d;
    --paper: #ffffff;
    --teal-deep: #003a45;
    --leaf-green: #7cc242;
    --ink: #1f2a2e;
    --rule-grey: #bdbdbd;
  }
  html, body {
    margin: 0;
    padding: 0;
    width: 1200px;
    height: 900px;
    overflow: hidden;
    background: var(--backdrop);
    font-family: "Lato", Arial, sans-serif;
  }
  .canvas {
    position: relative;
    width: 1200px;
    height: 900px;
  }
  .card {
    position: absolute;
    top: 200px;
    width: 310px;
    height: 502px;
    box-shadow: 3px 4px 6px rgba(0,0,0,0.45);
  }
  .card-front {
    left: 253px;
    background: var(--paper);
    border-radius: 62px 0 62px 0;
  }
  .card-back {
    left: 627px;
    background: var(--teal-deep);
    border-radius: 0 62px 0 62px;
  }
  .brand-name {
    position: absolute;
    left: 0;
    right: 0;
    margin: 0;
    text-align: center;
    font-weight: 900;
    letter-spacing: 1px;
    line-height: 1;
  }
  .card-front .brand-name {
    top: 114px;
    color: var(--teal-deep);
    font-size: 42px;
  }
  .card-back .brand-name {
    top: 206px;
    color: var(--paper);
    font-size: 48px;
  }
  .holder {
    position: absolute;
    left: 36px;
    top: 280px;
    color: var(--ink);
  }
  .holder-name {
    margin: 0;
    font-size: 18px;
    font-weight: 900;
    color: var(--teal-deep);
    letter-spacing: 0.3px;
  }
  .holder-title {
    margin: 0;
    font-size: 14px;
    line-height: 16px;
  }
  .contact-list {
    list-style: none;
    margin: 10px 0 0;
    padding: 0;
    font-size: 14px;
  }
  .contact-list li {
    display: flex;
    align-items: center;
    gap: 4px;
    height: 20px;
  }
  .contact-icon {
    width: 16px;
    height: 16px;
  }
  .office {
    margin: 9px 0 0;
    font-size: 14px;
    line-height: 18px;
    font-style: normal;
  }
  .office-company {
    font-weight: 700;
    color: var(--teal-deep);
  }
  .tagline {
    position: absolute;
    left: 32px;
    top: 447px;
    display: flex;
    align-items: center;
    gap: 8px;
  }
  .tagline-text {
    font-size: 14px;
    font-weight: 900;
    font-style: italic;
    color: var(--teal-deep);
  }
  .tagline-rule {
    width: 152px;
    height: 2px;
    background: var(--rule-grey);
  }
  .web-address {
    position: absolute;
    left: 0;
    right: 0;
    top: 445px;
    margin: 0;
    text-align: center;
    font-size: 13px;
    font-weight: 700;
    letter-spacing: 0.6px;
    color: var(--leaf-green);
  }
</style>
</head>
<body>
<main class="canvas">
  <section class="card card-front">
    <p class="brand-name">KAJU</p>
    <div class="holder">
      <h1 class="holder-name">MARCUS HALE</h1>
      <p class="holder-title">Managing Director</p>
      <ul class="contact-list">
        <li>
          <svg class="contact-icon" viewBox="0 0 16 16" aria-hidden="true">
            <circle cx="8" cy="8" r="7" fill="none" stroke="#7cc242" stroke-width="1.6"/>
            <path d="M4.5 7.5 Q8 4.5 11.5 7.5 L10.5 8.5 L9.4 7.6 L6.6 7.6 L5.5 8.5 Z M5.6 9 H10.4 V11 H5.6 Z" fill="#003a45"/>
          </svg>
          <span>044-987 654 321</span>
        </li>
        <li>
          <svg class="contact-icon" viewBox="0 0 16 16" aria-hidden="true">
            <circle cx="8" cy="8" r="7" fill="none" stroke="#7cc242" stroke-width="1.6"/>
            <rect x="4.3" y="5.3" width="7.4" height="5.4" fill="#003a45"/>
            <path d="M4.5 5.6 L8 8.4 L11.5 5.6" fill="none" stroke="#ffffff" stroke-width="0.9"/>
          </svg>
          <span>info@kajumail.example</span>
        </li>
      </ul>
      <address class="office">
        <span class="office-company">KAJU Freightways</span><br>
        421, Address line here<br>
        Country Name, 45452
      </address>
    </div>
    <div class="tagline">
      <span class="tagline-text">#ALLKAJU</span>
      <span class="tagline-rule"></span>
    </div>
  </section>

  <section class="card card-back">
    <p class="brand-name">KAJU</p>
    <p class="web-address">www.kajufreightco.example</p>
  </section>
</main>
</body>
</html>
```